Kampfsport Außenwerbung
Zielgruppe
Kampfsportschule für Kinder, Jugendliche und Erwachsene. Sportarten: Kick-Boxen, Jiu-Jitsu und Tricking
Aufgabenstellung
Ich bräuchte für meine Schaufenster eine schöne Außenwerbung. Beworben werden sollen alle meine Sportarten. Ich lade meinen Flyer hoch, damit im ähnlichen Stil gearbeitet werden kann. Außerdem auch noch andere Beispiele an denen man sich orientieren kann, sowie mein Logo und meine Fensterfront.

```html
<!DOCTYPE html>
<html lang="de">
<head>
<meta charset="utf-8">
<title>Martial Arts Borq – Schaufensterbeklebung</title>
<link rel="stylesheet" href="https://fonts.googleapis.com/css2?family=Open+Sans:wght@600;800&family=Philosopher:ital,wght@1,700&display=swap">
<style>
  :root {
    --page: #ededee;
    --frame: #dfe2e5;
    --frame-edge: #c9cdd1;
    --ink: #131313;
    --steel: #d3d3d6;
    --red: #d0121b;
    --red-light: #ff6b4a;
    --white: #ffffff;
    --cell-dark: #1d1d1f;
    --cell-grey: #e3e3e5;
  }
  html, body {
    margin: 0;
    width: 1200px;
    height: 1200px;
    overflow: hidden;
    background: var(--page);
  }
  .shopfront {
    position: absolute;
    left: 20px;
    top: 266px;
    width: 1160px;
    height: 668px;
  }
  .headline { font-family: "Philosopher", serif; font-style: italic; font-weight: 700; fill: var(--white); }
  .label { font-family: "Open Sans", sans-serif; font-weight: 800; fill: var(--white); }
  .label-italic { font-family: "Philosopher", serif; font-style: italic; font-weight: 700; fill: var(--white); }
  .contact { font-family: "Philosopher", serif; font-style: italic; font-weight: 700; fill: var(--white); }
  .brand-name { font-family: "Open Sans", sans-serif; font-weight: 800; fill: var(--white); }
  .schedule-text { font-family: "Open Sans", sans-serif; font-weight: 600; font-size: 5px; text-anchor: middle; }
  .schedule-text.on-dark { fill: var(--white); }
  .schedule-text.on-light { fill: var(--ink); }
  .day-name { font-family: "Open Sans", sans-serif; font-weight: 800; font-size: 5px; fill: var(--ink); text-anchor: middle; }
</style>
</head>
<body>
<svg class="shopfront" viewBox="-10 -10 1710 985" xmlns="http://www.w3.org/2000/svg">
  <defs>
    <linearGradient id="red-stripe" x1="0" y1="0" x2="1" y2="0">
      <stop offset="0" stop-color="var(--red)"/>
      <stop offset="1" stop-color="var(--red-light)"/>
    </linearGradient>
    <linearGradient id="photo-tone" x1="0" y1="0" x2="0" y2="1">
      <stop offset="0" stop-color="#3a2a2a"/>
      <stop offset="1" stop-color="#1a1a1a"/>
    </linearGradient>
    <linearGradient id="photo-tone-light" x1="0" y1="0" x2="0" y2="1">
      <stop offset="0" stop-color="#d9c9b8"/>
      <stop offset="1" stop-color="#eeeef0"/>
    </linearGradient>
    <clipPath id="glass-panes">
      <rect x="10" y="120" width="185" height="170"/>
      <rect x="225" y="105" width="200" height="165"/>
      <rect x="450" y="60" width="605" height="205"/>
      <rect x="1090" y="55" width="255" height="160"/>
      <rect x="1383" y="5" width="282" height="210"/>
      <rect x="13" y="315" width="187" height="545"/>
      <rect x="227" y="305" width="208" height="560"/>
      <rect x="485" y="320" width="245" height="550"/>
      <rect x="765" y="305" width="260" height="580"/>
      <rect x="1090" y="255" width="265" height="645"/>
      <rect x="1390" y="235" width="290" height="680"/>
    </clipPath>
  </defs>

  <!-- window frame -->
  <polygon class="window-frame" points="0,95 440,95 440,45 1375,45 1375,-5 1690,-5 1690,965 0,965" fill="var(--frame)" stroke="var(--frame-edge)" stroke-width="3"/>

  <!-- graphic across all panes -->
  <g class="pane-artwork" clip-path="url(#glass-panes)">
    <rect x="0" y="0" width="1690" height="960" fill="var(--ink)"/>
    <polygon points="0,320 0,620 620,0 320,0" fill="var(--steel)"/>
    <polygon points="250,960 520,960 1480,0 1210,0" fill="var(--steel)"/>
    <polygon points="900,960 1060,960 1690,330 1690,170" fill="var(--steel)"/>
    <polygon points="230,960 252,960 1212,0 1190,0" fill="url(#red-stripe)"/>
    <polygon points="1060,960 1075,960 1690,345 1690,330" fill="url(#red-stripe)"/>
    <polygon points="0,640 0,655 655,0 640,0" fill="url(#red-stripe)"/>

    <!-- headline bands -->
    <polygon points="470,175 1000,150 980,185 450,200" fill="url(#red-stripe)"/>
    <polygon points="450,210 900,190 880,225 450,240" fill="url(#red-stripe)"/>

    <!-- horizontal accent bars -->
    <rect x="13" y="420" width="187" height="12" fill="url(#red-stripe)"/>
    <rect x="13" y="660" width="420" height="6" fill="url(#red-stripe)"/>
    <rect x="485" y="760" width="540" height="24" fill="url(#red-stripe)" opacity="0.85"/>
    <rect x="1390" y="540" width="290" height="18" fill="url(#red-stripe)"/>
    <rect x="1450" y="580" width="230" height="22" fill="url(#red-stripe)"/>
    <rect x="1420" y="625" width="260" height="28" fill="url(#red-stripe)"/>
    <rect x="1390" y="680" width="290" height="4" fill="url(#red-stripe)"/>
    <rect x="1390" y="705" width="290" height="4" fill="url(#red-stripe)"/>
    <rect x="1390" y="730" width="290" height="4" fill="url(#red-stripe)"/>
    <rect x="1090" y="100" width="255" height="18" fill="url(#red-stripe)"/>
    <rect x="1090" y="140" width="255" height="24" fill="url(#red-stripe)"/>
    <rect x="1383" y="90" width="282" height="22" fill="url(#red-stripe)"/>

    <!-- photo areas -->
    <rect x="80" y="500" width="275" height="360" rx="30" fill="url(#photo-tone)" role="img" aria-label="Foto: Mädchen mit Kopfschutz und Boxhandschuhen beim Kick gegen einen Sandsack"/>
    <rect x="510" y="380" width="145" height="470" rx="30" fill="url(#photo-tone)" role="img" aria-label="Foto: Mädchen im Spagat im Stand beim Tricking, schwarzer Anzug mit gelbem Gurt"/>
    <rect x="1145" y="430" width="180" height="460" rx="30" fill="url(#photo-tone-light)" role="img" aria-label="Foto: Mädchen im weißen Kampfanzug mit gelbem Gurt in Kampfstellung"/>
  </g>

  <!-- headline -->
  <g class="headline-block" transform="rotate(-3 480 135)">
    <text class="headline" x="480" y="135" font-size="34">WIR MACHEN KINDER STARK</text>
    <text class="headline" x="500" y="178" font-size="30">KAMPSPORT &amp;</text>
    <text class="headline" x="505" y="220" font-size="30">SELBSTVERTEITIGUNG</text>
  </g>

  <!-- brand names -->
  <g class="brand brand-left">
    <circle cx="322" cy="370" r="16" fill="var(--red)"/>
    <text class="brand-name" x="322" y="410" font-size="17" text-anchor="middle">Martial Arts Borq</text>
  </g>
  <g class="brand brand-door">
    <circle cx="910" cy="485" r="11" fill="var(--red)"/>
    <text class="brand-name" x="910" y="515" font-size="13" text-anchor="middle">Martial Arts Borq</text>
  </g>
  <g class="brand brand-top">
    <circle cx="1524" cy="80" r="20" fill="var(--red)"/>
    <text class="brand-name" x="1524" y="135" font-size="22" text-anchor="middle">Martial Arts Borq</text>
  </g>

  <!-- discipline labels -->
  <text class="label-italic" x="43" y="715" font-size="36">KICK</text>
  <text class="label-italic" x="40" y="750" font-size="26">BOXEN</text>
  <text class="label" x="520" y="780" font-size="34" transform="rotate(-40 520 780)">TRICKING</text>
  <text class="label" x="1115" y="410" font-size="34" transform="rotate(-37 1115 410)">JIU JITSU</text>
  <text class="label" x="1115" y="465" font-size="24" transform="rotate(-37 1115 465)">Selbstverteitigung</text>

  <!-- contact -->
  <text class="contact" x="850" y="665" font-size="26" transform="rotate(-38 850 665)">0152 / 38 61 07 24</text>
  <text class="contact" x="858" y="710" font-size="17" transform="rotate(-38 858 710)">info@martial-arts-borq.de</text>

  <!-- timetable -->
  <g class="timetable" transform="translate(1405 382)">
    <rect x="0" y="0" width="267" height="150" rx="10" fill="var(--white)"/>
    <rect x="8" y="8" width="25" height="12" fill="var(--red)"/>
    <circle cx="20.5" cy="14" r="4" fill="none" stroke="var(--white)" stroke-width="1"/>
    <text class="day-name" x="57" y="16">MONTAG</text>
    <text class="day-name" x="102" y="16">DIENSTAG</text>
    <text class="day-name" x="147" y="16">MITTWOCH</text>
    <text class="day-name" x="192" y="16">DONNERSTAG</text>
    <text class="day-name" x="237" y="16">FREITAG</text>

    <g class="time-column">
      <rect x="8" y="22" width="25" height="22" fill="var(--red)"/>
      <text class="schedule-text on-dark" x="20.5" y="31">15:00</text><text class="schedule-text on-dark" x="20.5" y="38">15:50</text>
      <rect x="8" y="45" width="25" height="22" fill="var(--red)"/>
      <text class="schedule-text on-dark" x="20.5" y="54">16:00</text><text class="schedule-text on-dark" x="20.5" y="61">16:50</text>
      <rect x="8" y="68" width="25" height="22" fill="var(--red)"/>
      <text class="schedule-text on-dark" x="20.5" y="77">17:00</text><text class="schedule-text on-dark" x="20.5" y="84">18:50</text>
      <rect x="8" y="91" width="25" height="22" fill="var(--red)"/>
      <text class="schedule-text on-dark" x="20.5" y="100">18:15</text><text class="schedule-text on-dark" x="20.5" y="107">19:15</text>
      <rect x="8" y="114" width="25" height="22" fill="var(--red)"/>
      <text class="schedule-text on-dark" x="20.5" y="123">19:30</text><text class="schedule-text on-dark" x="20.5" y="130">21:00</text>
    </g>

    <!-- row 1 -->
    <rect x="35" y="22" width="44" height="22" fill="var(--cell-dark)"/>
    <text class="schedule-text on-dark" x="57" y="31">Kick-Boxen</text><text class="schedule-text on-dark" x="57" y="38">3-5 Jahre</text>
    <rect x="80" y="22" width="44" height="22" fill="var(--red)"/>
    <text class="schedule-text on-dark" x="102" y="31">Jiu-Jitsu</text><text class="schedule-text on-dark" x="102" y="38">3-6 Jahre</text>
    <rect x="125" y="22" width="44" height="22" fill="var(--cell-dark)"/>
    <text class="schedule-text on-dark" x="147" y="31">Kick-Boxen</text><text class="schedule-text on-dark" x="147" y="38">3-5 Jahre</text>
    <rect x="170" y="22" width="44" height="22" fill="var(--red)"/>
    <text class="schedule-text on-dark" x="192" y="31">Jiu-Jitsu</text><text class="schedule-text on-dark" x="192" y="38">3-6 Jahre</text>
    <rect x="215" y="22" width="44" height="22" fill="var(--white)"/>

    <!-- row 2 -->
    <rect x="35" y="45" width="44" height="22" fill="var(--cell-dark)"/>
    <text class="schedule-text on-dark" x="57" y="54">Kick-Boxen</text><text class="schedule-text on-dark" x="57" y="61">6-7 Jahre</text>
    <rect x="80" y="45" width="44" height="22" fill="var(--red)"/>
    <text class="schedule-text on-dark" x="102" y="54">Jiu-Jitsu</text><text class="schedule-text on-dark" x="102" y="61">7-12 Jahre</text>
    <rect x="125" y="45" width="44" height="22" fill="var(--cell-dark)"/>
    <text class="schedule-text on-dark" x="147" y="54">Kick-Boxen</text><text class="schedule-text on-dark" x="147" y="61">6-7 Jahre</text>
    <rect x="170" y="45" width="44" height="22" fill="var(--red)"/>
    <text class="schedule-text on-dark" x="192" y="54">Jiu-Jitsu</text><text class="schedule-text on-dark" x="192" y="61">7-12 Jahre</text>
    <rect x="215" y="45" width="44" height="22" fill="var(--cell-dark)"/>
    <text class="schedule-text on-dark" x="237" y="54">Kick-Boxen</text><text class="schedule-text on-dark" x="237" y="61">3-5 Jahre</text>

    <!-- row 3 -->
    <rect x="35" y="68" width="44" height="22" fill="var(--cell-dark)"/>
    <text class="schedule-text on-dark" x="57" y="77">Kick-Boxen</text><text class="schedule-text on-dark" x="57" y="84">8-10 Jahre</text>
    <rect x="80" y="68" width="44" height="22" fill="var(--cell-dark)"/>
    <text class="schedule-text on-dark" x="102" y="77">Tricking</text><text class="schedule-text on-dark" x="102" y="84">ab 6 Jahre</text>
    <rect x="125" y="68" width="44" height="22" fill="var(--cell-dark)"/>
    <text class="schedule-text on-dark" x="147" y="77">Kick-Boxen</text><text class="schedule-text on-dark" x="147" y="84">8-10 Jahre</text>
    <rect x="170" y="68" width="44" height="22" fill="var(--cell-dark)"/>
    <text class="schedule-text on-dark" x="192" y="77">Tricking</text><text class="schedule-text on-dark" x="192" y="84">ab 6 Jahre</text>
    <rect x="215" y="68" width="44" height="22" fill="var(--cell-dark)"/>
    <text class="schedule-text on-dark" x="237" y="75">Kick-Boxen</text><text class="schedule-text on-dark" x="237" y="81">ab 7 Jahre</text><text class="schedule-text on-dark" x="237" y="87">Ab Gelbgurt</text>

    <!-- row 4 -->
    <rect x="35" y="91" width="44" height="22" fill="var(--cell-dark)"/>
    <text class="schedule-text on-dark" x="57" y="100">Kick-Boxen</text><text class="schedule-text on-dark" x="57" y="107">10-12 Jahre</text>
    <rect x="80" y="91" width="44" height="22" fill="var(--cell-grey)"/>
    <text class="schedule-text on-light" x="102" y="100">Kick-Boxen</text><text class="schedule-text on-light" x="102" y="107">Ü25 Gruppe</text>
    <rect x="125" y="91" width="44" height="22" fill="var(--cell-dark)"/>
    <text class="schedule-text on-dark" x="147" y="100">Kick-Boxen</text><text class="schedule-text on-dark" x="147" y="107">10-12 Jahre</text>
    <rect x="170" y="91" width="44" height="22" fill="var(--cell-grey)"/>
    <text class="schedule-text on-light" x="192" y="100">Kick-Boxen</text><text class="schedule-text on-light" x="192" y="107">Ü25 Gruppe</text>
    <rect x="215" y="91" width="44" height="22" fill="var(--white)"/>

    <!-- row 5 -->
    <rect x="35" y="114" width="44" height="22" fill="var(--cell-dark)"/>
    <text class="schedule-text on-dark" x="57" y="123">Kick-Boxen</text><text class="schedule-text on-dark" x="57" y="130">ab 13 Jahre</text>
    <rect x="80" y="114" width="44" height="22" fill="var(--white)"/>
    <rect x="125" y="114" width="44" height="22" fill="var(--cell-dark)"/>
    <text class="schedule-text on-dark" x="147" y="123">Kick-Boxen</text><text class="schedule-text on-dark" x="147" y="130">ab 13 Jahre</text>
    <rect x="170" y="114" width="44" height="22" fill="var(--white)"/>
    <rect x="215" y="114" width="44" height="22" fill="var(--white)"/>
  </g>
</svg>
</body>
</html>
```